ORIM Holding

ORIM holding is located in the UAE. In the company, there are several departments covering Hospitality management, Facility Management, interior design and Construction.

The logo should not include the name holding, Just ORIM.

Needed Items:

(1) Logo.
(2) Business Card.
(3) Letterhead
(4) Envelope
(5) cd cover
(6) email signature
Updates

The previous brief was misplaced with another competition. Current update is the final.

Target Market(s)

Collaboration with international high end firms.

Industry/Entity Type

Business

Requirements
Must have
• COLOR PREFERENCE Maximum 2 colors, preferably mono-color with different shades.
Nice to have
• Elegant, luxurious, and minimalistic.

```html
<!DOCTYPE html>
<html lang="en">
<head>
<meta charset="utf-8">
<title>ORIM Holding — Business Card</title>
<link href="https://fonts.googleapis.com/css2?family=Lato:wght@400;700&family=Syncopate:wght@700&display=swap" rel="stylesheet">
<style>
  :root {
    --backdrop: #0f0f10;
    --card: #2a2b2e;
    --card-back: #25262a;
    --blue: #1a86d8;
    --text-grey: #b9bbbe;
    --rule: #55575b;
    --emboss: #3a3c40;
  }
  * { margin: 0; padding: 0; box-sizing: border-box; }
  html, body {
    width: 1200px; height: 820px; overflow: hidden;
    background: var(--backdrop);
    font-family: "Lato", Arial, sans-serif;
  }
  .stage { position: relative; width: 1200px; height: 820px; }
  .card {
    position: absolute; top: 255px;
    width: 525px; height: 300px;
    border-bottom: 3px solid var(--blue);
    border-left: 3px solid var(--blue);
  }
  .card--front { left: 50px; background: var(--card); }
  .card--back  { left: 625px; background: var(--card-back); }

  .brand {
    position: absolute;
    font-family: "Lato", Arial, sans-serif;
    font-weight: 700;
    letter-spacing: 3px;
    white-space: nowrap;
  }
  .card--front .brand {
    right: 40px; top: 48px;
    font-size: 34px; color: var(--blue);
  }
  .card--back .brand {
    left: 0; right: 0; top: 118px; text-align: center;
    font-size: 46px; color: var(--emboss);
  }

  .person { position: absolute; left: 36px; right: 28px; top: 124px; }
  .person__row {
    display: flex; align-items: flex-end; gap: 12px;
  }
  .person__name {
    font-family: "Syncopate", "Arial Black", sans-serif;
    font-weight: 700;
    font-size: 16px; line-height: 20px;
    color: var(--blue); letter-spacing: 0.5px;
    white-space: nowrap; flex: none;
  }
  .person__divider {
    flex: 1; height: 1px; background: var(--rule);
    margin-bottom: 5px;
  }
  .person__title {
    font-size: 14px; color: var(--text-grey); margin-top: 4px;
  }
  .contacts {
    position: absolute; left: 36px; bottom: 28px;
    list-style: none;
  }
  .contacts li {
    display: flex; align-items: center; gap: 10px;
    font-size: 14px; color: var(--text-grey); line-height: 26px;
  }
  .contacts svg { width: 14px; height: 14px; flex: none; }
  .contacts .accent { color: var(--blue); }
  .address {
    position: absolute; right: 36px; top: 166px;
    font-style: normal;
    font-size: 13px; color: var(--text-grey); line-height: 20px;
  }
</style>
</head>
<body>
<main class="stage">
  <section class="card card--front">
    <div class="brand">ORIM HOLDING</div>
    <div class="person">
      <div class="person__row">
        <div class="person__name">DANIEL HARPER</div>
        <div class="person__divider"></div>
      </div>
      <div class="person__title">Managing Director</div>
    </div>
    <address class="address">
      18, Marina Crescent Road<br>Dubai, UAE, 50231
    </address>
    <ul class="contacts">
      <li>
        <svg viewBox="0 0 24 24" fill="none" stroke="#1a86d8" stroke-width="2.4" stroke-linecap="round"><path d="M5 3h4l2 5-2.5 1.5a11 11 0 0 0 6 6L16 13l5 2v4a2 2 0 0 1-2 2A17 17 0 0 1 3 5a2 2 0 0 1 2-2z"/></svg>
        044-555 010 246
      </li>
      <li>
        <svg viewBox="0 0 24 24" fill="#1a86d8"><path d="M2 5h20v14H2z"/><path d="M2 5l10 8 10-8" fill="none" stroke="#2a2b2e" stroke-width="2"/></svg>
        info@orimgroup.ae
      </li>
      <li>
        <svg viewBox="0 0 24 24" fill="none" stroke="#1a86d8" stroke-width="2"><circle cx="12" cy="12" r="10"/><path d="M2 12h20M12 2c3 3 3 17 0 20M12 2c-3 3-3 17 0 20"/></svg>
        <span>www.<span class="accent">orimgroup</span>.ae</span>
      </li>
    </ul>
  </section>

  <section class="card card--back">
    <div class="brand">ORIM HOLDING</div>
  </section>
</main>
</body>
</html>
```